Brindovalle Business cards

Dear team, I need to get the design file to suit it to our team. The focus of the business card is the Automotive Market and the design must be in black colour and the logo must be in glossy black. On the front of the card I need to get the following info:

- Name and Surname
- Title
- eMail
- Phone Number
- Skype account
- domain address

```html
<!DOCTYPE html>
<html lang="es">
<head>
<meta charset="utf-8">
<title>Brindovalle – Tarjetas de visita</title>
<link rel="stylesheet" href="https://fonts.googleapis.com/css2?family=Montserrat:wght@400;800&display=swap">
<style>
  :root {
    --stage: #3a3a3a;
    --card: #2b2b2d;
    --gloss-dark: #141416;
    --gloss-mid: #3c3c40;
    --gloss-light: #8e8e94;
    --tile-line: rgba(255,255,255,0.07);
    --red: #e4202a;
    --white: #ffffff;
    --grey-text: #e6e6e6;
  }
  * { box-sizing: border-box; margin: 0; padding: 0; }
  html, body { width: 1200px; height: 1186px; overflow: hidden; }
  body {
    background: var(--stage);
    font-family: "Montserrat", sans-serif;
    position: relative;
  }
  .card {
    position: absolute;
    left: 120px;
    width: 960px;
    height: 540px;
    border-radius: 34px;
    background: var(--card);
    overflow: hidden;
  }
  .card--back { top: 40px; }
  .card--front { top: 610px; }

  .pattern-fill {
    position: absolute; inset: 0;
    background:
      repeating-linear-gradient(90deg, var(--tile-line) 0 2px, transparent 2px 80px),
      repeating-linear-gradient(0deg, var(--tile-line) 0 2px, transparent 2px 80px),
      linear-gradient(135deg, rgba(255,255,255,0.14) 0%, rgba(255,255,255,0) 45%),
      linear-gradient(160deg, var(--gloss-mid) 0%, var(--card) 45%, var(--gloss-dark) 100%);
  }

  .gloss-panel {
    position: absolute;
    right: 40px; top: 40px;
    width: 420px; height: 400px;
    border-radius: 24px;
    background: linear-gradient(150deg, var(--gloss-light) 0%, var(--gloss-mid) 35%, var(--gloss-dark) 80%);
    opacity: 0.8;
  }

  .brand {
    position: absolute;
    left: 70px; top: 78px;
    display: flex; align-items: center; gap: 20px;
  }
  .brand__mark { width: 56px; height: 56px; background: var(--red); }
  .brand__name {
    color: var(--white);
    font-weight: 800;
    font-size: 50px;
    letter-spacing: -0.5px;
  }

  .person { position: absolute; left: 120px; top: 212px; }
  .person__name {
    color: var(--red);
    font-weight: 800;
    font-size: 30px;
    letter-spacing: 0.5px;
    text-transform: uppercase;
  }
  .person__title {
    color: var(--grey-text);
    font-weight: 400;
    font-size: 22px;
    margin-top: 2px;
  }

  .address {
    position: absolute; left: 120px; top: 318px;
    color: var(--grey-text);
    font-style: normal;
    font-weight: 400; font-size: 20px; line-height: 28px;
  }

  .contacts {
    position: absolute; left: 120px; top: 392px;
    list-style: none;
  }
  .contacts li {
    display: flex; align-items: center; gap: 14px;
    color: var(--grey-text);
    font-size: 20px; line-height: 31px;
  }
  .contacts svg { width: 18px; height: 18px; fill: var(--red); flex: none; }
</style>
</head>
<body>

  <section class="card card--back" aria-label="Reverso de la tarjeta">
    <div class="pattern-fill" role="img" aria-label="Patrón repetido del símbolo de la marca en negro brillante"></div>
  </section>

  <section class="card card--front" aria-label="Anverso de la tarjeta">
    <div class="gloss-panel" role="img" aria-label="Símbolo grande de la marca en negro brillante"></div>

    <div class="brand">
      <span class="brand__mark"></span>
      <span class="brand__name">Brindovalle</span>
    </div>

    <div class="person">
      <p class="person__name">Marco Ledesma</p>
      <p class="person__title">Comercial</p>
    </div>

    <address class="address">
      Pol. Ind. Arvena, C/4 nº 12<br>
      41820 Villanueva del Sol
    </address>

    <ul class="contacts">
      <li>
        <svg viewBox="0 0 24 24" aria-hidden="true"><path d="M6.6 10.8a15 15 0 0 0 6.6 6.6l2.2-2.2a1 1 0 0 1 1-.25 11.4 11.4 0 0 0 3.6.57 1 1 0 0 1 1 1V20a1 1 0 0 1-1 1A17 17 0 0 1 3 4a1 1 0 0 1 1-1h3.5a1 1 0 0 1 1 1c0 1.25.2 2.45.57 3.57a1 1 0 0 1-.25 1z"/></svg>
        600 41 27 58
      </li>
      <li>
        <svg viewBox="0 0 24 24" aria-hidden="true"><path d="M2 5h20v14H2z M2 5l10 8 10-8"/></svg>
        redazione@brindovalle.com
      </li>
      <li>
        <svg viewBox="0 0 24 24" aria-hidden="true"><circle cx="12" cy="12" r="10"/></svg>
        @brindovalle
      </li>
      <li>
        <svg viewBox="0 0 24 24" aria-hidden="true"><path d="M12 2a10 10 0 1 0 0 20 10 10 0 0 0 0-20zm0 2c.9 1.2 1.6 3 1.9 5H10.1c.3-2 1-3.8 1.9-5zM4.3 14a8 8 0 0 1 0-4h3.8a17 17 0 0 0 0 4zm1 2h3.1c.3 1.4.8 2.7 1.4 3.7A8 8 0 0 1 5.3 16zm3.1-8H5.3a8 8 0 0 1 4.5-3.7C9.2 5.3 8.7 6.6 8.4 8zM12 20c-.9-1.2-1.6-3-1.9-4h3.8c-.3 1-1 2.8-1.9 4zm2.2-6H9.8a15 15 0 0 1 0-4h4.4a15 15 0 0 1 0 4zm0 5.7c.6-1 1.1-2.3 1.4-3.7h3.1a8 8 0 0 1-4.5 3.7zM15.9 14a17 17 0 0 0 0-4h3.8a8 8 0 0 1 0 4z"/></svg>
        www.brindovalle.com
      </li>
    </ul>
  </section>

</body>
</html>
```